Business Cards for IT Consulting Company (Managed Service Provider)

I am looking to have some business cards printed and would like some designs. We are an IT Consulting company based in Vancouver BC. I would like a nice clean and modern look to the cards. I have uploaded all the versions of my logo so parts can be used as needed. Here is a snippit from our website homepage:

Quillbrook Networks Ltd. is an IT Solutions Partner located in Vancouver BC, Canada. We offer IT solutions and support to customers in the greater Vancouver Area. With expertise in Microsoft platforms, as well as Linux and Mac OSX and over 12 years experience in the IT industry, Quillbrook Networks is dedicated to offering our clients top quality service and products. We take pride in the solutions we offer our customers. The greatest compliment a client can give us is to recommend our services.

Quillbrook Networks Ltd. offers a wide range of IT services from onsite service to remote support and managed service solutions. This allows clients to choose the support path that best suits their company’s needs. Supporting many different sized companies from small to enterprise level over the past 12 years Quillbrook Networks has the experience and expertise needed to ensure things run smoothly. Allowing our clients to focus on doing business.

Revolutionizing the way IT services are delivered.

Quillbrook Networks is dedicated to providing our clients with IT solutions that work and grow with them for years to come. This philosophy helps save money in the long run instead of replacing equipment constantly. Far too often IT solutions are not well thought out and while possibly solving the problem at hand, require replacement due to growth or quality within a very short time frame. Quillbrook Networks takes pride in providing solutions that will last and be able to accommodate growth without the need for replacement.

Industry/Entity Type

Information Technology

Contact Information for Business Card

Quillbrook Networks Ltd.
(Employee Name)
Eml: (Employees Email Address)
Web: quillbrook.me
Ph: 604-555-0148

Font styles to use
Serif
Sans Serif

Requirements
Must have
• The Company logo and company colors.
Nice to have
• - Our tag line: "Revolutionizing IT Services" or "Revolutionizing the way IT services are delivered."
• - Also I really like the idea of nature and technology together blending which is sort of where my logo came from so integrating that somehow onto the business cards would be great.

```html
<!DOCTYPE html>
<html lang="en">
<head>
<meta charset="utf-8">
<title>Quillbrook Networks Ltd. – Business Card</title>
<link href="https://fonts.googleapis.com/css2?family=Montserrat:wght@500;600&family=Roboto:ital,wght@0,400;0,500;1,400&display=swap" rel="stylesheet">
<style>
  :root {
    --backdrop: #a8a6a6;
    --paper: #f3f3f2;
    --brand-blue: #1b8fd4;
    --brand-grey: #5f6062;
    --ink: #3d3e40;
    --white: #ffffff;
  }
  * { margin: 0; padding: 0; box-sizing: border-box; }
  html, body {
    width: 1200px; height: 1200px; overflow: hidden;
    background: var(--backdrop);
  }
  .canvas { position: relative; width: 1200px; height: 1200px; }

  .card {
    position: absolute;
    width: 712px; height: 419px;
    background: var(--paper);
    overflow: hidden;
  }
  .card--front { left: 238px; top: 118px; }
  .card--back  { left: 230px; top: 643px; }

  /* Front */
  .front-brand {
    position: absolute; left: 110px; top: 140px;
    display: flex; align-items: center; gap: 22px;
  }
  .brand-dot {
    flex: none;
    width: 78px; height: 78px; border-radius: 50%;
    background: var(--brand-blue);
  }
  .brand-name {
    font-family: "Montserrat", sans-serif;
    font-weight: 600;
    color: var(--brand-blue);
    line-height: 1;
    white-space: nowrap;
  }
  .front-brand .brand-name .main { display: block; font-size: 70px; letter-spacing: -1px; }
  .front-brand .brand-name .sub  { display: block; font-size: 24px; letter-spacing: 1px; margin-top: 4px; }

  .tagline {
    position: absolute; left: 0; right: 0; top: 376px;
    display: flex; align-items: center; justify-content: center; gap: 16px;
    font-family: "Montserrat", sans-serif; font-weight: 500;
    font-size: 18px; color: var(--ink);
  }
  .tagline .rule { width: 112px; height: 3px; background: var(--brand-blue); border-radius: 2px; }

  /* Back */
  .back-shapes { position: absolute; inset: 0; }
  .back-brand {
    position: absolute; left: 116px; top: 362px;
    transform: rotate(-90deg); transform-origin: left top;
    display: flex; align-items: center; gap: 12px;
  }
  .back-brand .brand-dot { width: 44px; height: 44px; }
  .back-brand .brand-name .main { display: block; font-size: 42px; letter-spacing: -1px; }
  .back-brand .brand-name .sub  { display: block; font-size: 15px; letter-spacing: 1px; margin-top: 3px; }

  .contact {
    position: absolute; left: 392px; top: 128px;
    font-family: "Roboto", sans-serif; color: var(--white);
  }
  .contact .name { font-size: 25px; font-weight: 500; }
  .contact .role { font-size: 16px; font-style: italic; margin-top: 4px; }
  .contact ul { list-style: none; margin-top: 26px; }
  .contact li {
    display: flex; align-items: center; gap: 18px;
    font-size: 18px; line-height: 27px;
  }
  .contact svg { width: 17px; height: 17px; flex: none; }
</style>
</head>
<body>
<main class="canvas">

  <section class="card card--front">
    <div class="front-brand">
      <span class="brand-dot"></span>
      <span class="brand-name"><span class="main">quillbrook</span><span class="sub">NETWORKS LTD.</span></span>
    </div>
    <p class="tagline"><span class="rule"></span>Revolutionizing IT Services<span class="rule"></span></p>
  </section>

  <section class="card card--back">
    <svg class="back-shapes" viewBox="0 0 712 419" width="712" height="419">
      <path d="M228 0 H246 Q318 150 276 330 Q300 160 228 0 Z" fill="var(--brand-grey)"/>
      <path d="M256 0 Q352 210 248 419 H712 V0 Z" fill="var(--brand-blue)"/>
    </svg>

    <div class="back-brand">
      <span class="brand-dot"></span>
      <span class="brand-name"><span class="main">quillbrook</span><span class="sub">NETWORKS LTD.</span></span>
    </div>

    <div class="contact">
      <p class="name">Daniel Mercer</p>
      <p class="role">Managing Director</p>
      <ul>
        <li>
          <svg viewBox="0 0 24 24"><path fill="#fff" d="M6.6 10.8a15 15 0 0 0 6.6 6.6l2.2-2.2c.3-.3.7-.4 1-.2 1.1.4 2.3.6 3.6.6.6 0 1 .4 1 1V20c0 .6-.4 1-1 1A17 17 0 0 1 3 4c0-.6.4-1 1-1h3.5c.6 0 1 .4 1 1 0 1.3.2 2.5.6 3.6.1.3 0 .7-.2 1z"/></svg>
          604-555-0148
        </li>
        <li>
          <svg viewBox="0 0 24 24" fill="none" stroke="#fff" stroke-width="2"><circle cx="12" cy="12" r="9"/><path d="M3 12h18M12 3c3 3 3 15 0 18M12 3c-3 3-3 15 0 18"/></svg>
          www.quillbrook.me
        </li>
        <li>
          <svg viewBox="0 0 24 24"><rect x="2" y="5" width="20" height="14" fill="#fff"/><path d="M2 5l10 8 10-8" fill="none" stroke="var(--brand-blue)" stroke-width="1.6"/></svg>
          support@quillbrook.me
        </li>
      </ul>
    </div>
  </section>

</main>
</body>
</html>
```